Need App for Impact Related Events

My app is to help with internal events. When you enter the prompted event code the next screen shows you everyone currently at the event. It will give you the ability to Start a conversation with someone you met at that event, or signal it is your turn to send a message. The next screen is a message thread with that person. I am looking for a design that incorporates the colors and ‘feel good’ emotion of our logo. I have pieced together a pretty good interpretation of what I’m looking for in the attached mockup by slicing and dicing designs. I also attached our logo mascot.Screens (see attached mockups)

Note 1: I do not like the picture on the screen used in screen one because it makes it seem like a dating app. I attached an alternative photo that can be used or present different ideas.

Note 2: On the login/signup screen (screen 2) I need an additional first and last name for login, you can try to fit this on one login screen or present a two step signup screen where that is presented in the second screen.

READ MOCKUP GUIDELINES UNDER Must Haves

Target Market(s)

People attending internal social impact events

Industry/Entity Type

Charity

Font styles to use
Sans Serif

Colors
86cfc6

Requirements
Must have
• Follow the screen mockups attached to project
• PLEASE READ
• I have provided a relatively close design of what I’m looking for in the mockups. Some screens need to be followed more closely to my design mockup than other. I have listed a guide below how how closely you should follow my mockup design exactly. Overall I would like to see some ideas of incorporating a few accent colors so it doesn’t appear SO Blue. I also attached some app inspiration designs I found from around the web
• Screen Mockup Guideline Follow %
• Screen 1: 65% - mostly on target, would like to see ways to make it not SO Blue and possibly creative places to add some explainer text describing the app
• Screen 2: 50% - general design idea is here, but more open
• Screen 3: 35% - a lot more room for design influence
• Screen 4: 70% - mostly on target, a little room for design influence/color scheme ideas
• Screen 5-6: 25% - a lot of room for design change/ideas/influence
• Screen 7-8: 80% - already very close to what I need, maybe open to slight sizing and color scheme ideas
• Screen 9: 15% - the most open for influence, only the general functionality of the screen is communicated here
Nice to have
• Please Read Mockup Guideline above. In large part I am looking for something to use some nice accent colors so it is not overwhelmingly blue and bring the whole design into a seamless style.
Should not have

```html
<!DOCTYPE html>
<html lang="en">
<head>
<meta charset="utf-8">
<title>Hum Kindly – App Screens 5–8</title>
<link href="https://fonts.googleapis.com/css2?family=Nunito+Sans:wght@400;600;700;800&display=swap" rel="stylesheet">
<style>
:root{
  --bg:#efefef;
  --ink:#1d1d1f;
  --text:#3c3c44;
  --muted:#6c6c76;
  --teal:#3fd2c4;
  --teal-2:#4bd7dc;
  --teal-soft:#d9f6f2;
  --card:#ffffff;
  --bubble:#ececee;
  --screen-tint:#f6f7f9;
  --accent-blue:#6aa9f2;
  --accent-pink:#e86fb4;
  --accent-orange:#f4a26a;
  --accent-purple:#8b7fe0;
  --avatar:#c9b8aa;
}
*{box-sizing:border-box;margin:0;padding:0}
html,body{width:1200px;height:1200px;overflow:hidden}
body{background:var(--bg);font-family:"Nunito Sans",sans-serif;color:var(--text);position:relative}
.brand{position:absolute;left:745px;top:170px;display:flex;align-items:center;gap:16px}
.brand-dot{width:34px;height:34px;border-radius:50%;background:var(--teal)}
.brand-name{font-size:56px;font-weight:700;color:var(--ink);letter-spacing:-1px}
.step{position:absolute;top:386px;width:40px;text-align:center;font-size:19px;font-weight:800;color:var(--ink)}
.screen{position:absolute;top:437px;width:234px;height:510px;background:#fff;border-radius:28px;overflow:hidden;box-shadow:0 6px 24px rgba(0,0,0,.06)}
.screen-tall{height:536px}
.home-bar{position:absolute;bottom:9px;left:50%;width:86px;height:4px;margin-left:-43px;border-radius:2px;background:#c9c9cc}
.blob{position:absolute;border-radius:50%;background:var(--teal-soft)}
.mini-brand{position:absolute;left:0;right:0;display:flex;justify-content:center;align-items:center;gap:6px;font-size:13px;font-weight:700;color:var(--ink)}
.mini-brand i{width:12px;height:12px;border-radius:50%;background:var(--teal)}
.screen-title{position:absolute;left:0;right:0;text-align:center;font-size:13px;font-weight:600;letter-spacing:.6px;color:var(--text)}
.field{position:absolute;left:21px;width:190px;height:39px;background:#fff;border-radius:4px;box-shadow:0 4px 14px rgba(0,0,0,.07);display:flex;align-items:center;justify-content:center;font-size:12px;color:var(--ink)}
.go-button{position:absolute;left:83px;top:300px;width:66px;height:66px;border-radius:50%;background:linear-gradient(135deg,var(--teal-2),var(--teal));display:flex;align-items:center;justify-content:center;box-shadow:0 6px 14px rgba(63,210,196,.35)}
.header{position:absolute;left:0;top:0;width:234px}
.status{position:absolute;top:12px;left:19px;right:14px;display:flex;justify-content:space-between;align-items:center;color:#fff;font-size:10px;font-weight:600}
.header-title{position:absolute;top:44px;left:0;right:0;text-align:center;color:#fff;font-size:12.5px;font-weight:800;letter-spacing:.5px}
.back{position:absolute;top:46px;left:10px}
.search{position:absolute;left:8px;top:79px;width:218px;height:33px;background:#fff;border-radius:17px;box-shadow:0 3px 10px rgba(0,0,0,.06);display:flex;align-items:center;padding-left:18px;font-size:9.5px;color:var(--muted)}
.search .sep{width:1px;height:14px;background:#ddd;margin:0 14px 0 10px}
.section-label{position:absolute;left:17px;top:132px;font-size:9.5px;color:var(--text)}
.friend{position:absolute;left:9px;width:217px;height:54px;background:#fff;border-radius:3px;border-left:2px solid;box-shadow:0 3px 10px rgba(0,0,0,.05);display:flex;align-items:center;padding-left:12px}
.avatar{width:36px;height:36px;border-radius:50%;background:var(--avatar);position:relative;flex:none}
.avatar .presence{position:absolute;right:-2px;top:0;width:8px;height:8px;border-radius:50%;background:var(--teal);border:1px solid #fff}
.avatar .presence.off{background:#d6d6d6}
.friend-info{margin-left:11px;flex:1}
.friend-name{font-size:12.5px;color:var(--text)}
.friend-note{font-size:7.5px;color:var(--muted);margin-top:1px}
.friend-action{margin-right:14px}
.load-more{position:absolute;left:0;right:0;top:487px;text-align:center;font-size:12px;font-weight:600;letter-spacing:.4px;color:var(--text)}
.thread-avatar{position:absolute;left:91px;top:79px;width:52px;height:52px;border-radius:50%;background:var(--avatar);border:2px solid #fff}
.thread-avatar .presence{position:absolute;right:-3px;top:2px;width:10px;height:10px;border-radius:50%;background:#fff;border:2px solid var(--teal)}
.bubble{position:absolute;font-size:9.5px;line-height:13.5px;border-radius:3px;display:flex;align-items:center;padding:0 12px}
.bubble.in{left:12px;width:186px;height:38px;background:var(--bubble);color:var(--text)}
.bubble.out{left:38px;width:186px;height:40px;background:#fff;color:var(--text);padding-left:13px}
.stamp{position:absolute;font-size:7.5px;color:var(--muted)}
.stamp.in{left:16px}
.stamp.out{right:10px}
.composer{position:absolute;left:0;width:234px;height:46px;background:#fff}
.composer-line{position:absolute;left:15px;right:15px;bottom:4px;height:1px;background:#e2e2e2}
.composer-text{position:absolute;left:20px;top:14px;font-size:9.5px;color:var(--muted)}
.composer-send{position:absolute;right:22px;top:12px}
.code-box{position:absolute;left:24px;top:227px;width:189px;height:40px;background:#fff;border-radius:4px;box-shadow:0 4px 14px rgba(0,0,0,.07);display:flex;align-items:center;justify-content:center;font-size:17px;letter-spacing:.5px;color:var(--ink)}
.code-help{position:absolute;left:0;right:0;top:284px;text-align:center;font-size:11.5px;line-height:19px;letter-spacing:.2px;color:var(--text);white-space:nowrap}
</style>
</head>
<body>

<div class="brand">
  <span class="brand-dot"></span>
  <span class="brand-name">Hum Kindly</span>
</div>

<div class="step" style="left:141px">5</div>
<div class="step" style="left:436px">6</div>
<div class="step" style="left:727px">7</div>
<div class="step" style="left:1021px">8</div>

<!-- Screen 5: enter location code -->
<section class="screen" style="left:42px">
  <div class="blob" style="left:150px;top:-10px;width:110px;height:110px;opacity:.35"></div>
  <div class="blob" style="left:146px;top:36px;width:18px;height:18px"></div>
  <div class="blob" style="left:190px;top:360px;width:110px;height:110px"></div>
  <div class="blob" style="left:5px;top:400px;width:20px;height:20px"></div>
  <div class="blob" style="left:35px;top:404px;width:9px;height:9px"></div>
  <div class="mini-brand" style="top:92px"><i></i>Hum Kindly</div>
  <div class="screen-title" style="top:200px">ENTER LOCATION KIND CODE</div>
  <div class="field" style="top:235px">Enter code here</div>
  <div class="go-button">
    <svg width="24" height="24" viewBox="0 0 24 24" fill="none" stroke="#fff" stroke-width="2" stroke-linecap="round" stroke-linejoin="round"><path d="M3 12h18M14 5l7 7-7 7"/></svg>
  </div>
  <div class="home-bar"></div>
</section>

<!-- Screen 6: friends list -->
<section class="screen screen-tall" style="left:336px;background:var(--screen-tint)">
  <svg class="header" width="234" height="100" viewBox="0 0 234 100" aria-hidden="true">
    <defs><linearGradient id="hdr6" x1="0" x2="1"><stop offset="0" stop-color="#3fd2b8"/><stop offset="1" stop-color="#4bd7dc"/></linearGradient></defs>
    <path d="M0 0H234V92Q234 84 200 84H34Q0 84 0 96Z" fill="url(#hdr6)"/>
  </svg>
  <div class="status"><span>9:41</span><span>▮▮ ◠ ▬</span></div>
  <svg class="back" width="10" height="14" viewBox="0 0 10 14" fill="none" stroke="#fff" stroke-width="1.6"><path d="M7 2 2 7l5 5"/></svg>
  <div class="header-title">YOUR FRIENDS</div>
  <div class="search">
    <svg width="13" height="13" viewBox="0 0 13 13" fill="none" stroke="#8a8a92" stroke-width="1.3"><circle cx="5.5" cy="5.5" r="4.3"/><path d="M8.7 8.7 12 12"/></svg>
    <span class="sep"></span>Search here
  </div>
  <div class="section-label">Who you’ve met so far</div>

  <div class="friend" style="top:149px;border-color:var(--accent-blue)">
    <div class="avatar" role="img" aria-label="Profile photo of Nora T. Hale"><span class="presence"></span></div>
    <div class="friend-info"><div class="friend-name">Nora T. Hale</div></div>
    <svg class="friend-action" width="18" height="18" viewBox="0 0 24 24" fill="var(--teal)"><path d="M22 2 2 10l7 3 3 8z"/></svg>
  </div>
  <div class="friend" style="top:215px;border-color:var(--accent-pink)">
    <div class="avatar" role="img" aria-label="Profile photo of Lena Marsh"><span class="presence"></span></div>
    <div class="friend-info"><div class="friend-name">Lena Marsh</div></div>
    <svg class="friend-action" width="16" height="18" viewBox="0 0 16 18" fill="none" stroke="var(--teal)" stroke-width="2" stroke-linecap="round"><path d="M4 16V7a4 4 0 0 1 8 0v3M9 8l3 3 3-3"/></svg>
  </div>
  <div class="friend" style="top:280px;border-color:var(--accent-orange)">
    <div class="avatar" role="img" aria-label="Profile photo of Peter K. Rowe"><span class="presence off"></span></div>
    <div class="friend-info"><div class="friend-name">Peter K. Rowe</div><div class="friend-note">Lorem Ipsum is simply dum...</div></div>
    <svg class="friend-action" width="8" height="12" viewBox="0 0 8 12" fill="none" stroke="#555" stroke-width="1.3"><path d="m2 2 4 4-4 4"/></svg>
  </div>
  <div class="friend" style="top:346px;border-color:var(--accent-purple)">
    <div class="avatar" role="img" aria-label="Profile photo of Dylan M. Foss"><span class="presence"></span></div>
    <div class="friend-info"><div class="friend-name">Dylan M. Foss</div><div class="friend-note">Standard dummy text ever ...</div></div>
    <svg class="friend-action" width="8" height="12" viewBox="0 0 8 12" fill="none" stroke="#555" stroke-width="1.3"><path d="m2 2 4 4-4 4"/></svg>
  </div>
  <div class="friend" style="top:411px;border-color:var(--accent-purple)">
    <div class="avatar" role="img" aria-label="Profile photo of Omar Venn"><span class="presence"></span></div>
    <div class="friend-info"><div class="friend-name">Omar Venn</div><div class="friend-note">Standard dummy text ever ...</div></div>
    <svg class="friend-action" width="8" height="12" viewBox="0 0 8 12" fill="none" stroke="#555" stroke-width="1.3"><path d="m2 2 4 4-4 4"/></svg>
  </div>
  <div class="load-more">TAP TO LOAD MORE (65)</div>
  <div class="home-bar"></div>
</section>

<!-- Screen 7: message thread -->
<section class="screen" style="left:629px;background:var(--screen-tint)">
  <svg class="header" width="234" height="110" viewBox="0 0 234 110" aria-hidden="true">
    <defs><linearGradient id="hdr7" x1="0" x2="1"><stop offset="0" stop-color="#3fd2b8"/><stop offset="1" stop-color="#4bd7dc"/></linearGradient></defs>
    <path d="M0 0H234V90Q117 130 0 90Z" fill="url(#hdr7)"/>
  </svg>
  <div class="status"><span>9:41</span><span>▮▮ ◠ ▬</span></div>
  <svg class="back" width="10" height="14" viewBox="0 0 10 14" fill="none" stroke="#fff" stroke-width="1.6"><path d="M7 2 2 7l5 5"/></svg>
  <div class="header-title">LENA MARSH</div>
  <div class="thread-avatar" role="img" aria-label="Profile photo of Lena Marsh"><span class="presence"></span></div>

  <div class="bubble in" style="top:153px">Who you’ve met so far</div>
  <div class="stamp in" style="top:198px">1 day ago</div>
  <div class="bubble out" style="top:218px">Lorem Ipsum has been the industry’s standard dummy text ever</div>
  <div class="stamp out" style="top:264px">1 day ago</div>
  <div class="bubble in" style="top:283px">Who you’ve met so far</div>
  <div class="stamp in" style="top:329px">1 day ago</div>
  <div class="bubble out" style="top:348px">Lorem Ipsum has been the industry’s standard dummy text ever</div>
  <div class="stamp out" style="top:394px">1 day ago</div>

  <div class="composer" style="top:446px">
    <div class="composer-text">Type your message here</div>
    <svg class="composer-send" width="17" height="17" viewBox="0 0 24 24" fill="var(--teal)"><path d="M22 2 2 10l7 3 3 8z"/></svg>
    <div class="composer-line"></div>
  </div>
  <div class="home-bar"></div>
</section>

<!-- Screen 8: your kind code -->
<section class="screen" style="left:926px">
  <div class="blob" style="left:150px;top:-10px;width:110px;height:110px;opacity:.35"></div>
  <div class="blob" style="left:146px;top:36px;width:18px;height:18px"></div>
  <div class="blob" style="left:190px;top:360px;width:110px;height:110px"></div>
  <div class="blob" style="left:5px;top:400px;width:20px;height:20px"></div>
  <div class="blob" style="left:35px;top:404px;width:9px;height:9px"></div>
  <div class="mini-brand" style="top:98px"><i></i>Hum Kindly</div>
  <div class="screen-title" style="top:192px">YOUR KIND CODE</div>
  <div class="code-box">JGHEYS747JRH</div>
  <p class="code-help">Give this code to the people<br>at your location or event to allow<br>them to connect to each<br>other - kind of like a wifi password</p>
  <div class="home-bar"></div>
</section>

</body>
</html>
```